Beautiful design for wordpress

I need a beautiful, colourful and feminine website. My business is called 'The Velvet Lantern', and I sell crystals, books, CD's, pendulums and other metaphysical items. I also provide Reiki (energy healing).
I want this design to be eye catching and inspire happiness and joy in those who see it. And I would love to see the use of the logo and its colours :)
Please add these on the web design: Home, About, Online store, Blog

Industry/Entity Type

Business

Requirements
Must have
• Colourful and playful, must use the logo somewhere, have the words on a menu saying 'Home, Blog, Online store and about' (or similar to those)And the design must stand out!
Should not have
• grey, brown and other boring colours.

```html
<!DOCTYPE html>
<html lang="en">
<head>
<meta charset="utf-8">
<title>The Velvet Lantern</title>
<link href="https://fonts.googleapis.com/css2?family=Crimson+Text:ital,wght@0,400;0,600;1,400;1,600&family=Great+Vibes&family=Arimo:wght@400;700&display=swap" rel="stylesheet">
<style>
:root{
  --green:#8aaa1e;
  --green-dark:#6f8c12;
  --orange:#e07a1f;
  --ink:#333;
  --muted:#777;
  --line:#e2e2e2;
  --footer:#252525;
  --footer-bottom:#1b1b1b;
  --paper:#fff;
}
*{box-sizing:border-box;margin:0;padding:0}
html,body{width:736px;height:1200px;overflow:hidden;background:var(--paper)}
body{position:relative;font-family:"Crimson Text",Georgia,serif;color:var(--ink)}
.abs{position:absolute}
.top-rule{left:0;top:0;width:736px;height:3px;background:var(--green)}
.brand{left:80px;top:22px;display:flex;align-items:center;gap:6px}
.brand-dot{width:12px;height:12px;border-radius:50%;background:var(--green)}
.brand-name{font-size:15px;font-weight:600;color:var(--green-dark);line-height:1}
.cart{right:80px;top:16px;font-size:10.5px;color:var(--muted);display:flex;align-items:center;gap:5px}
.cart b{color:var(--green);font-weight:600}
.main-nav{top:49px;left:391px;display:flex;gap:0;font-size:11.5px}
.main-nav a{color:#222;text-decoration:none;margin-right:24px}
.main-nav a.active{color:var(--green)}
.main-nav a:last-child{margin-right:0}
.hero{left:81px;top:74px;width:574px;height:318px;background:radial-gradient(ellipse at 28% 40%,#6b6360 0%,#3a3534 35%,#151313 75%)}
.hero-title{left:368px;top:142px;font-size:27px;font-style:italic;font-weight:600;color:var(--green);white-space:nowrap}
.hero-copy{left:372px;top:196px;width:266px;font-size:7.6px;line-height:20.8px;color:#eee;text-align:center}
.buy{left:427px;top:278px;height:28px;display:flex;font-size:14px;font-weight:600;color:#fff}
.buy .price{background:var(--green-dark);padding:0 7px;line-height:28px}
.buy .act{background:var(--green);padding:0 11px;line-height:28px}
.dots{left:606px;top:372px;display:flex;gap:6px}
.dots span{width:6px;height:6px;border-radius:50%;background:#e59a1a}
.dots span:first-child{background:var(--green)}
.banner{left:81px;top:392px;width:574px;height:134px;background:#f3f3f3;border:1px solid #ececec}
.ring-l{left:97px;top:410px;width:118px;height:90px;background:radial-gradient(ellipse,#d9d9d9,#f3f3f3 70%)}
.ring-r{left:508px;top:412px;width:108px;height:96px;background:radial-gradient(ellipse,#cfcfcf,#f3f3f3 70%)}
.banner-title{left:0;width:736px;text-align:center;top:394px;font-family:"Great Vibes",cursive;font-size:42px;color:var(--green)}
.banner-copy{left:228px;width:280px;top:462px;text-align:center;font-size:8.6px;line-height:18px;color:#555}
.sec-title{font-size:14px;color:#333}
.sec-rule{left:170px;top:555px;width:278px;height:1px;background:var(--line)}
.arrows{left:457px;top:547px;font-size:10px;color:#bbb;letter-spacing:4px}
.card{top:583px;width:127px;height:179px;border:1px solid var(--line);text-align:center}
.card .thumb{margin:4px auto 0;width:90px;height:82px;border-radius:4px}
.card h3{font-weight:400;font-size:15px;color:var(--orange);margin-top:10px}
.card p{font-size:7.5px;color:#555;margin-top:4px}
.btn{display:inline-block;border:1px solid #ccc;font-size:8.5px;color:#555;padding:6px 21px}
.card .btn{margin-top:10px}
.store-copy{left:496px;top:582px;width:158px;font-family:"Arimo",Arial,sans-serif;font-size:6.4px;line-height:14.3px;color:#888}
.store-btn{left:499px;top:724px}
.post{top:824px;display:flex;gap:8px;width:190px}
.post .pic{position:relative;width:77px;height:75px;flex:none}
.post .date{position:absolute;right:0;top:0;width:18px;height:18px;background:var(--green);color:#fff;font-size:6.5px;line-height:8px;text-align:center;padding-top:1px;font-family:"Arimo",Arial,sans-serif}
.post h4{font-weight:400;font-size:8.4px;color:var(--green);margin-bottom:6px}
.post p{font-family:"Arimo",Arial,sans-serif;font-size:6.6px;line-height:12px;color:#666;padding-left:2px}
.newsletter{left:80px;top:926px;width:576px;height:69px;border:1px solid var(--line)}
.nl-title{left:90px;top:940px;font-size:25px;color:var(--green)}
.nl-field{left:227px;top:944px;width:320px;height:30px;border:1px solid var(--line);display:flex;align-items:center;gap:6px;padding-left:9px;font-family:"Arimo",Arial,sans-serif;font-size:7px;color:#999}
.nl-submit{left:547px;top:944px;width:62px;height:30px;background:var(--green);color:#fff;font-size:9.5px;font-weight:600;text-align:center;line-height:30px;letter-spacing:.5px}
.footer{left:0;top:1006px;width:736px;height:154px;background:var(--footer);font-family:"Arimo",Arial,sans-serif;color:#eee}
.fcol{position:absolute;top:22px}
.fcol h5{font-weight:400;font-size:9.5px;margin-bottom:12px;color:#f2f2f2}
.fcol li{list-style:none;font-size:6.6px;line-height:15.6px;color:#ddd}
.contact-row{display:flex;gap:8px;font-size:6.6px;line-height:9.5px;color:#ddd;margin-bottom:10px}
.contact-row svg{flex:none;margin-top:1px}
.footer-bottom{left:0;top:1160px;width:736px;height:40px;background:var(--footer-bottom);font-family:"Arimo",Arial,sans-serif}
.copy{position:absolute;left:81px;top:16px;font-size:6.2px;color:#eee;font-weight:700}
.social{position:absolute;left:533px;top:10px;display:flex;gap:6px}
.social span{width:20px;height:20px;border:1.5px solid #eee;border-radius:50%}
</style>
</head>
<body>
<div class="abs top-rule"></div>

<header>
  <div class="abs brand"><span class="brand-dot"></span><span class="brand-name">The Velvet Lantern</span></div>
  <div class="abs cart">
    <svg width="11" height="11" viewBox="0 0 11 11"><path d="M1.5 3.5h8v6.5h-8z M3.5 3.5V2a2 2 0 0 1 4 0v1.5" fill="none" stroke="#888" stroke-width="1"/></svg>
    CART 0 items for <b>$0.00</b>
  </div>
  <nav class="abs main-nav">
    <a class="active" href="#">Home</a><a href="#">About</a><a href="#">Online store</a><a href="#">Blog</a><a href="#">Contact us</a>
  </nav>
</header>

<section>
  <div class="abs hero" role="img" aria-label="Photograph of a woman wearing a diamond drop earring and ring on a dark background"></div>
  <h1 class="abs hero-title">Neque porro quisquam</h1>
  <p class="abs hero-copy">Standard dummy text ever since the 1500s, when an unknown printer took a galley of type and scrambled it to make a type specimen book. It has survived not but also the leap into electronic typesetting,</p>
  <div class="abs buy"><span class="price">$ 22.00</span><span class="act">BUY NOW</span></div>
  <div class="abs dots"><span></span><span></span><span></span><span></span></div>
</section>

<section>
  <div class="abs banner"></div>
  <div class="abs ring-l" role="img" aria-label="Photograph of diamond rings"></div>
  <div class="abs ring-r" role="img" aria-label="Photograph of silver wedding rings"></div>
  <h2 class="abs banner-title">I sell crystals</h2>
  <p class="abs banner-copy">Duis aute irure dolor in reprehenderit in voluptate velit esse cillum dolore eu fugiat nulla pariatur. Excepteur sint occaecat cupidatat non proident</p>
</section>

<section>
  <h2 class="abs sec-title" style="left:81px;top:546px">Latest Products</h2>
  <div class="abs sec-rule"></div>
  <div class="abs arrows">‹ ›</div>
  <div class="abs card" style="left:81px">
    <div class="thumb" role="img" aria-label="Pink healing crystal cluster" style="background:linear-gradient(160deg,#f3b7f0,#c75fc7 55%,#c9a67a)"></div>
    <h3>Healing Crystals</h3><p>Sed sapien sapien,...</p><span class="btn">VIEW ALL</span>
  </div>
  <div class="abs card" style="left:216px">
    <div class="thumb" role="img" aria-label="Stack of colourful books" style="background:linear-gradient(180deg,#e54b3c,#f5a623 35%,#f2e23a 55%,#7dc242 80%)"></div>
    <h3>Sell Book</h3><p>Sed sapien sapien,...</p><span class="btn">VIEW ALL</span>
  </div>
  <div class="abs card" style="left:351px">
    <div class="thumb" role="img" aria-label="Stack of compact discs" style="background:radial-gradient(ellipse,#8fd0f0,#3c7fc4 55%,#fff 75%)"></div>
    <h3>Sell CD</h3><p>Sed sapien sapien,...</p><span class="btn">VIEW ALL</span>
  </div>

  <h2 class="abs sec-title" style="left:491px;top:546px">Online store</h2>
  <p class="abs store-copy">Sed ut perspiciatis unde omnis iste natus error sit voluptatem accusantium doloremque laudantium, totam rem aperiam, eaque ipsa quae ab illo inventore veritatis et quasi architecto beatae vitae dicta sunt explicabo. Nemo enim ipsam voluptatem quia voluptas sit aspernatur aut odit aut fugit, sed quia consequuntur magni dolores eos qui ratione voluptatem sequi nesciunt quia voluptas sit aspermagni dolores eos qui ratione .....</p>
  <span class="abs btn store-btn">READ MORE</span>
</section>

<section>
  <h2 class="abs sec-title" style="left:81px;top:795px">Latest Blog</h2>
  <article class="abs post" style="left:81px">
    <div class="pic" role="img" aria-label="Hands holding tumbled crystals" style="background:linear-gradient(135deg,#9c6b5c,#c58e7e 50%,#5c6f8a)"><span class="date">22<br>Apr</span></div>
    <div><h4>Neque quisquam dolorem</h4><p>Virginia, looked up one of the more obscure Latin words, consectetur, from a Lorem Ipsum passage, and going through the source.</p></div>
  </article>
  <article class="abs post" style="left:279px">
    <div class="pic" role="img" aria-label="Pastel crystals and gemstones" style="background:linear-gradient(135deg,#cfe3f2,#f2c9a8 50%,#b59ad1)"><span class="date">22<br>Apr</span></div>
    <div><h4>Neque quisquam dolorem</h4><p>Virginia, looked up one of the more obscure Latin words, consectetur, from a Lorem Ipsum passage, and going through the source.</p></div>
  </article>
  <article class="abs post" style="left:478px">
    <div class="pic" role="img" aria-label="Polished colourful stones" style="background:linear-gradient(135deg,#2e8a8a,#d08a3a 50%,#8a3a2e)"><span class="date">22<br>Apr</span></div>
    <div><h4>Neque quisquam dolorem</h4><p>Virginia, looked up one of the more obscure Latin words, consectetur, from a Lorem Ipsum passage, and going through the source.</p></div>
  </article>
</section>

<section>
  <div class="abs newsletter"></div>
  <h2 class="abs nl-title">Newsletter</h2>
  <div class="abs nl-field">
    <svg width="16" height="10" viewBox="0 0 16 10"><rect x="0.5" y="0.5" width="15" height="9" fill="#ccc"/><path d="M0.5 0.5l7.5 5 7.5-5" fill="none" stroke="#fff"/></svg>
    Entr Your Email id :
  </div>
  <div class="abs nl-submit">SUBMIT</div>
</section>

<footer class="abs footer">
  <div class="fcol" style="left:85px"><h5>Information</h5><ul><li>About us</li><li>Delivery Information</li><li>Privacy Policy</li><li>Terms &amp; Condition</li><li>Contact Us</li></ul></div>
  <div class="fcol" style="left:190px"><h5>My Account</h5><ul><li>My Orders</li><li>My Credit Slips</li><li>My Addresses</li><li>My Personal Info</li></ul></div>
  <div class="fcol" style="left:290px"><h5>Customer Service</h5><ul><li>My Account</li><li>Order History</li><li>Wish List</li><li>Newsletter</li><li>Returns</li><li>Site Map</li></ul></div>
  <div class="fcol" style="left:403px"><h5>Shipping Info</h5><ul><li>Delivery</li><li>Return</li><li>Service</li><li>Gift cart</li><li>Mobile</li><li>Manufacturers</li></ul></div>
  <div class="fcol" style="left:510px;width:160px"><h5>Contact Us</h5>
    <div class="contact-row"><svg width="8" height="11" viewBox="0 0 8 11"><path d="M4 0.5a3.5 3.5 0 0 1 3.5 3.5c0 2.5-3.5 6.5-3.5 6.5S0.5 6.5 0.5 4A3.5 3.5 0 0 1 4 0.5z" fill="#bbb"/><circle cx="4" cy="4" r="1.3" fill="#252525"/></svg><span>Lantern Row: Suite 12, Willow Court<br>48 Meadow Lane<br>Ashford, Kent</span></div>
    <div class="contact-row"><svg width="8" height="10" viewBox="0 0 8 10"><path d="M1.5 0.5l2 2-1 1.5c.6 1.5 1.5 2.5 2.8 3.2l1.4-1 1.8 2-1.5 1.5C3.5 9 0 5 0.3 1.8z" fill="#bbb"/></svg><span>Phone: 555-014-2207<br>Fax: 555-019-3381</span></div>
    <div class="contact-row"><svg width="10" height="7" viewBox="0 0 10 7"><rect width="10" height="7" fill="#bbb"/><path d="M0 0l5 4 5-4" fill="none" stroke="#252525"/></svg><span>info@velvetlantern.example</span></div>
  </div>
</footer>

<div class="abs footer-bottom">
  <p class="copy">Copyright 2014 the velvet lantern. All Right Reserved.</p>
  <div class="social" aria-label="Social links"><span></span><span></span><span></span><span></span><span></span></div>
</div>
</body>
</html>
```